Career-focused learning application platform

We have a K-12 learning application platform designed for grades 6-12 that needs user interface improvements that provide a positive experience for all users (teachers and students). The learning platform provides career-focused math curriculum and career exploration resources. We would like to improve the user-interface with engaging design elements without taking away from the functionality and performance of the platform.

```html
<!DOCTYPE html>
<html lang="en">
<head>
<meta charset="utf-8">
<title>CareerTrail Learning Platform</title>
<link href="https://fonts.googleapis.com/css2?family=Poppins:wght@400;500;600;700&display=swap" rel="stylesheet">
<style>
:root{
  --teal:#0f5c5a;
  --teal-dark:#0b4d4b;
  --orange:#f4572a;
  --orange-soft:#fde9e0;
  --cream:#fbf7f3;
  --grey:#eeeeee;
  --line:#e2e2e2;
  --ink:#1d1d1d;
  --muted:#555;
}
*{box-sizing:border-box;margin:0;padding:0}
html,body{width:1200px;height:2959px;overflow:hidden;background:#fff;font-family:"Poppins",sans-serif;color:var(--ink)}
.panel{position:absolute;left:80px;width:1037px;background:#fff;box-shadow:0 4px 18px rgba(0,0,0,.12);overflow:hidden}
.abs{position:absolute}
.brand{font-weight:700;color:var(--orange);display:flex;align-items:center;gap:8px}
.brand .dot{width:14px;height:14px;border-radius:50%;background:var(--orange)}
.btn{display:flex;align-items:center;justify-content:center;background:var(--orange);color:#fff;border-radius:22px;font-weight:500;font-size:13px;white-space:nowrap}
/* sign-in */
.signin{top:103px;height:666px}
.signin .form{left:0;top:0;width:520px;height:666px}
.signin .art{left:520px;top:0;width:517px;height:666px;background:radial-gradient(circle at 65% 45%,#fff 0 30%,transparent 31%),linear-gradient(160deg,#fbe0cc,#f6d2b7 60%,#f3c3a0)}
.signin h1{position:absolute;top:114px;width:520px;text-align:center;font-size:41px;line-height:43px;font-weight:700}
.sso{position:absolute;top:217px;width:195px;height:61px;background:var(--teal);color:#fff;font-size:25px;display:flex;align-items:center;justify-content:center;gap:10px;border-radius:3px}
.sso .sq{width:24px;height:24px;background:#fff}
.sso .ci{width:26px;height:26px;border-radius:50%;background:#fff}
.divider{position:absolute;top:311px;left:32px;width:460px;border-top:1px solid #ccc}
.divider span{position:absolute;left:50%;transform:translate(-50%,-50%);background:#fff;padding:0 12px;font-size:13px;color:var(--muted);white-space:nowrap}
.label{position:absolute;left:32px;font-size:15px;color:#333}
.input{position:absolute;left:32px;width:460px;height:50px;border:1px solid var(--line);border-radius:3px}
/* app shell */
.topbar{position:absolute;left:0;top:0;width:100%;height:65px;background:#fff;box-shadow:0 2px 6px rgba(0,0,0,.08);z-index:2}
.topbar .brand{position:absolute;left:14px;top:20px;font-size:17px}
.user{position:absolute;left:818px;top:10px;display:flex;align-items:center;gap:12px;font-size:15px;font-weight:600;white-space:nowrap}
.avatar{width:42px;height:42px;border-radius:50%;background:#c9d3d6}
.sidebar{position:absolute;left:0;top:65px;width:141px;bottom:0;background:var(--teal)}
.sidebar a{display:block;height:48px;line-height:48px;padding-left:22px;color:#fff;font-size:13px;text-decoration:none;font-weight:500;margin-top:5px}
.sidebar a.on{background:var(--orange)}
.main{position:absolute;left:141px;top:65px;right:0;bottom:0;background:var(--cream)}
.card{position:absolute;left:25px;width:851px;background:#fff;border-radius:6px;box-shadow:0 1px 6px rgba(0,0,0,.08)}
.band{background:var(--teal);color:#fff;border-radius:6px 6px 0 0}
.tabs{position:absolute;left:35px;display:flex;gap:34px;font-size:13px;font-weight:500}
.tabs .cur{color:var(--orange)}
/* lessons */
.lessons{position:absolute;left:21px;top:108px;width:809px;height:343px;border:1px solid #eee}
.lessons .head{height:52px;background:var(--grey);display:flex;align-items:center;justify-content:space-between;padding:0 14px 0 18px;font-size:14px;font-weight:600}
.lesson{position:absolute;left:18px;width:752px;height:80px;border:1px solid #eee;box-shadow:0 1px 4px rgba(0,0,0,.06);background:#fff}
.lesson .folder{position:absolute;left:18px;top:24px;width:44px;height:36px;background:#f2c94c;border-radius:3px}
.lesson .t{position:absolute;left:74px;top:12px;font-size:12.5px}
.lesson .d{position:absolute;left:76px;top:32px;width:450px;font-size:11px;line-height:19px;color:#444}
.lesson .due{position:absolute;left:578px;top:12px;font-size:11.5px;font-weight:600}
.lesson .btn{position:absolute;left:576px;top:34px;width:132px;height:32px;font-size:12px}
.gear{position:absolute;left:720px;top:40px;width:18px;height:18px;border-radius:50%;border:5px solid #111}
.promo{position:absolute;left:25px;top:575px;width:851px;height:222px;background:var(--teal);color:#fff;border-radius:6px}
.promo h2{position:absolute;left:32px;top:20px;font-size:23px;font-weight:600}
.promo h3{position:absolute;left:32px;top:54px;font-size:16px;font-weight:500}
.promo p{position:absolute;left:32px;top:86px;font-size:12.5px;line-height:24px;white-space:nowrap}
.promo .btn{position:absolute;left:35px;top:161px;width:131px;height:32px;font-size:12px}
.preview{position:absolute;left:528px;top:18px;width:301px;height:187px;background:#fff;border-radius:6px;color:#333;font-size:5px;text-align:center;padding:10px 14px}
/* profiler */
.cols{position:absolute;top:288px;width:386px;height:483px;background:#fff;border:1px solid #eee}
.row{position:absolute;left:15px;display:flex;align-items:center;font-size:15px}
.badge{width:48px;height:48px;border-radius:50%;background:var(--teal);color:#fff;display:flex;align-items:center;justify-content:center;font-size:21px;font-weight:500;margin-right:11px;flex:none}
.row .name{width:120px}
.row .score{width:36px;font-size:18px;font-weight:600}
.bar{width:131px;height:34px;border-radius:17px;background:var(--orange-soft);overflow:hidden}
.bar i{display:block;height:100%;background:var(--orange);border-radius:17px 0 0 17px}
.saved{position:absolute;left:22px;top:779px;width:851px;height:182px;background:var(--teal);color:#fff;border-radius:6px;padding:20px 35px;font-size:16px;line-height:30px}
.saved h2{font-size:23px;font-weight:600;line-height:34px}
</style>
</head>
<body>

<section class="panel signin">
  <div class="abs form">
    <div class="brand abs" style="left:190px;top:38px;font-size:22px"><span class="dot"></span>CareerTrail</div>
    <h1>Sign in with your<br>school account</h1>
    <div class="sso" style="left:63px"><span class="sq"></span>Northgate</div>
    <div class="sso" style="left:268px"><span class="ci"></span>Orbitly</div>
    <div class="divider"><span>Or continue with</span></div>
    <div class="label" style="top:334px">Email address</div>
    <div class="input" style="top:366px"></div>
    <div class="label" style="top:428px">Password</div>
    <div class="input" style="top:459px"></div>
    <div class="abs" style="left:34px;top:524px;width:18px;height:18px;border:1px solid #ccc;border-radius:3px"></div>
    <div class="abs" style="left:63px;top:524px;font-size:13px">Remember me</div>
    <div class="btn abs" style="left:169px;top:565px;width:188px;height:45px;font-size:15px">Sign In</div>
    <div class="abs" style="left:0;top:624px;width:520px;text-align:center;font-size:14px;color:#444">Need an account? <span style="color:#2a6fd6;text-decoration:underline">Register here</span></div>
  </div>
  <div class="abs art" role="img" aria-label="Illustration of students and a teacher launching a rocket beside a light bulb, gears and web layouts"></div>
</section>

<section class="panel" style="top:851px;height:880px">
  <header class="topbar">
    <div class="brand"><span class="dot"></span>CareerTrail</div>
    <svg class="abs" style="left:728px;top:22px" width="26" height="26" viewBox="0 0 26 26" fill="none" stroke="#111" stroke-width="2"><circle cx="11" cy="11" r="8"/><path d="M17 17l7 7"/></svg>
    <svg class="abs" style="left:774px;top:20px" width="24" height="28" viewBox="0 0 24 28" fill="none" stroke="#111" stroke-width="2"><path d="M4 20V12a8 8 0 0116 0v8l2 3H2zM9 25h6"/><circle cx="18" cy="22" r="4" fill="#f4572a" stroke="none"/></svg>
    <div class="user"><span class="avatar"></span>okafor@lpath.edu</div>
  </header>
  <nav class="sidebar">
    <a>Home</a><a>Career Tools ⌄</a><a class="on">Classes</a><a>Assessments</a>
  </nav>
  <main class="main">
    <div class="abs" style="left:28px;top:20px;font-size:14px">⟵&nbsp; Browse All Classes</div>
    <div class="card" style="top:64px;height:488px">
      <div class="band" style="height:64px;padding:12px 15px;font-size:13.5px;line-height:20px">Math Teacher<br>Period 1 &nbsp;&nbsp;| &nbsp;8th Grade Math/Pre-Algebra</div>
      <div class="btn abs" style="left:538px;top:16px;width:143px;height:34px">Class Roster</div>
      <div class="btn abs" style="left:692px;top:16px;width:144px;height:34px">Class Settings</div>
      <div class="tabs" style="top:78px"><span class="cur">» LESSONS</span><span>ADD LESSON</span></div>
      <div class="lessons">
        <div class="head"><span>⌄ &nbsp;UPCOMING LESSONS</span><span class="btn" style="width:132px;height:32px;font-size:12px">▤ ADD LESSON</span></div>
        <div class="lesson" style="top:66px"><span class="folder"></span><div class="t">1.1: TRANSLATIONS</div><div class="d">Career Spotlight: Aerospace Engineers, Civil Engineers, Aerospace Technicians, Carpenters, Interior Decorators</div><div class="due">Due: 10/15 at 11:59PM</div><div class="btn">Begin Lesson</div><span class="gear"></span></div>
        <div class="lesson" style="top:157px"><span class="folder"></span><div class="t">1.1: TRANSLATIONS</div><div class="d">Career Spotlight: Aerospace Engineers, Civil Engineers, Aerospace Technicians, Carpenters, Interior Decorators</div><div class="due">Due: 10/15 at 11:59PM</div><div class="btn">Begin Lesson</div><span class="gear"></span></div>
        <div class="lesson" style="top:248px"><span class="folder"></span><div class="t">1.1: TRANSLATIONS</div><div class="d">Career Spotlight: Aerospace Engineers, Civil Engineers, Aerospace Technicians, Carpenters, Interior Decorators</div><div class="due">Due: 10/15 at 11:59PM</div><div class="btn">Begin Lesson</div><span class="gear"></span></div>
        <div class="abs" style="left:800px;top:150px;width:4px;height:40px;background:var(--teal)"></div>
      </div>
    </div>
    <div class="promo">
      <h2>CT Assessments</h2>
      <h3>Looking for your upcoming CT Assessments?</h3>
      <p>The CT Assessments are designed to be taken 3 times a year at the<br>beginning of the year, the middle of the year, and the end of the year.<br>Navigate over to CT Assessments now to to see what's coming up!</p>
      <div class="btn">Go there now!</div>
      <div class="preview">
        <div style="display:flex;justify-content:space-between;font-weight:600"><span>End of Year Assessment</span><span>Instructions</span></div>
        <div style="margin-top:36px;line-height:8px">Welcome to the End of Year assessment.<br>This test has multiple choice questions with four answers.<br>Take your time and read each one.<br>Click the flag to mark a question for review.<br>Do not refresh the page during the test.</div>
        <div class="abs" style="right:14px;bottom:8px;width:40px;height:6px;background:var(--teal)"></div>
      </div>
    </div>
  </main>
</section>

<section class="panel" style="top:1806px;height:1057px">
  <header class="topbar">
    <div class="brand"><span class="dot"></span>CareerTrail</div>
    <svg class="abs" style="left:728px;top:22px" width="26" height="26" viewBox="0 0 26 26" fill="none" stroke="#111" stroke-width="2"><circle cx="11" cy="11" r="8"/><path d="M17 17l7 7"/></svg>
    <svg class="abs" style="left:774px;top:20px" width="24" height="28" viewBox="0 0 24 28" fill="none" stroke="#111" stroke-width="2"><path d="M4 20V12a8 8 0 0116 0v8l2 3H2zM9 25h6"/><circle cx="18" cy="22" r="4" fill="#f4572a" stroke="none"/></svg>
    <div class="user"><span class="avatar"></span>okafor@lpath.edu</div>
  </header>
  <nav class="sidebar">
    <a>Home</a><a class="on">Career Tools ⌄</a><a>Classes</a><a>Assessments</a>
  </nav>
  <main class="main">
    <div class="abs" style="left:29px;top:10px;font-size:24px;font-weight:500">Tea Cher</div>
    <div class="card" style="top:65px;height:688px">
      <div class="band" style="height:57px;padding:12px 15px;font-size:24px;font-weight:500">Profiler Results</div>
      <div class="tabs" style="top:89px"><span class="cur">» LESSONS</span><span>ADD LESSON</span></div>
      <div class="abs" style="left:21px;top:108px;width:809px;height:50px;background:var(--grey);font-size:15px;font-weight:600">
        <span class="abs" style="left:37px;top:14px">CATEGORY</span><span class="abs" style="left:218px;top:14px">SCORE</span>
        <span class="abs" style="left:444px;top:14px">CATEGORY</span><span class="abs" style="left:625px;top:14px">SCORE</span>
      </div>
      <div class="cols" style="left:30px;top:172px">
        <div class="row" style="top:14px"><span class="badge">A</span><span class="name">Artisic</span><span class="score">26</span><span class="bar"><i style="width:52%"></i></span></div>
        <div class="row" style="top:80px"><span class="badge">S</span><span class="name">social</span><span class="score">26</span><span class="bar"><i style="width:52%"></i></span></div>
        <div class="row" style="top:146px"><span class="badge">I</span><span class="name">Inerstigative</span><span class="score">19</span><span class="bar"><i style="width:44%"></i></span></div>
        <div class="row" style="top:212px"><span class="badge">E</span><span class="name">Enterprising</span><span class="score">19</span><span class="bar"><i style="width:44%"></i></span></div>
        <div class="row" style="top:278px"><span class="badge">R</span><span class="name">Realistic</span><span class="score">16</span><span class="bar"><i style="width:38%"></i></span></div>
        <div class="row" style="top:344px"><span class="badge">C</span><span class="name">Conventions</span><span class="score">12</span><span class="bar"><i style="width:32%"></i></span></div>
        <div class="btn abs" style="left:101px;top:415px;width:172px;height:44px;font-size:15px">Retake Matcher</div>
      </div>
      <div class="cols" style="left:432px;top:172px">
        <div class="row" style="top:14px"><span class="badge">W</span><span style="line-height:20px">Working<br>Conditions</span></div>
        <div class="row" style="top:80px"><span class="badge">S</span><span>Support</span></div>
        <div class="row" style="top:146px"><span class="badge">R</span><span>Relationships</span></div>
        <div class="row" style="top:212px"><span class="badge">RC</span><span>Recognition</span></div>
        <div class="row" style="top:278px"><span class="badge">I</span><span>Independence</span></div>
        <div class="row" style="top:344px"><span class="badge">A</span><span>Achievement</span></div>
        <div class="btn abs" style="left:101px;top:415px;width:172px;height:44px;font-size:15px">Retake Matcher</div>
      </div>
    </div>
    <div class="saved">
      <h2>SAVED CAREERS</h2>
      <div>Retail Salespersons</div>
      <div><b style="font-weight:600">Median Wage:</b> No information available</div>
      <div><b style="font-weight:600">Annual openings:</b> 12,090</div>
      <div><b style="font-weight:600">Growth :</b> -7.0%</div>
      <div class="btn abs" style="left:745px;top:12px;width:98px;height:34px;font-size:12px">View All</div>
    </div>
  </main>
</section>

</body>
</html>
```